Vernac Law Business cards and stationary design project

We are looking for a stationary design for business cards (double sided), 8x10, 5x7, and legal and standard envelopes.

We would like the design to match the logo that we have already.
Color palate preferred is Teal, White, grey and any others that will look good for a professional law firm.

We would like this statement: "RELATIONSHIPS. RESPECT. RESULT" to be on the back of the business cards and maybe on the stationary if it looks good.

Please see link to website for more information: www.vernac-law.example

Target Market(s)

Potential clients that need Attorney services.

Industry/Entity Type

Law Firm

Contact Information for Business Card

We would like the front and back to be two different colors. Current business cards are teal front, grey back and are a vertical design. We are open to options with colors.

Font styles to use
Serif

Colors
33a6d7
33b8a4
b9b9b9
5c5c5c

Requirements
Must have
• Logo supplied needs to go on the card and stationary.
• Match website color palate, www.vernac-law.example
• Be professional and not too wordy.
• Criminal Law, Civil Litigation, Personal Injury, Restraining Orders need to be on the card.
Nice to have
• CLARITY. COUNSEL. COMMITMENT. on the back of the card.
Should not have
• Not be too busy/wordy or too flashy.

```html
<!DOCTYPE html>
<html lang="en">
<head>
<meta charset="utf-8">
<title>Vernac Law – Business Card</title>
<link rel="stylesheet" href="https://fonts.googleapis.com/css2?family=Cinzel:wght@400;500;600&family=Tinos&display=swap">
<style>
  :root {
    --teal: #0f8898;
    --teal-back: #11889a;
    --white: #ffffff;
    --grey-text: #555555;
    --stage: #4a4a4a;
  }
  * { box-sizing: border-box; margin: 0; padding: 0; }
  html, body { width: 1105px; height: 1200px; overflow: hidden; }
  body {
    background: var(--stage);
    position: relative;
    font-family: "Tinos", "Times New Roman", serif;
  }
  .card {
    position: absolute;
    left: 196px;
    width: 720px;
  }
  .card-front { top: 146px; height: 412px; background: var(--white); }
  .card-back { top: 602px; height: 410px; background: var(--teal-back); }

  .person-name {
    position: absolute; left: 36px; top: 28px;
    font-family: "Cinzel", Georgia, serif; font-weight: 500;
    font-size: 31px; line-height: 38px; letter-spacing: 1px; color: var(--teal);
  }
  .person-title {
    position: absolute; left: 36px; top: 67px;
    font-family: "Cinzel", Georgia, serif;
    font-size: 20px; line-height: 26px; letter-spacing: 1.5px; color: var(--grey-text);
  }
  .contact-list, .practice-list {
    position: absolute; left: 36px; list-style: none;
    font-size: 20px; color: var(--grey-text);
  }
  .contact-list { top: 181px; }
  .practice-list { top: 285px; }
  .contact-list li, .practice-list li {
    height: 30px; display: flex; align-items: center;
  }
  .contact-list li { gap: 14px; }
  .contact-icon { width: 18px; height: 18px; fill: var(--teal); flex: none; }
  .practice-list li::before {
    content: ""; width: 6px; height: 6px; border-radius: 50%; flex: none;
    background: var(--teal); margin: 0 20px 0 6px;
  }

  .firm-name {
    position: absolute; right: 35px; top: 322px;
    font-family: "Cinzel", Georgia, serif;
    font-size: 31px; line-height: 40px; letter-spacing: 1px; color: var(--teal);
  }

  .firm-name-large {
    position: absolute; left: 0; right: 0; top: 172px; text-align: center;
    font-family: "Cinzel", Georgia, serif;
    font-size: 54px; line-height: 64px; letter-spacing: 2px; color: var(--white);
  }
  .tagline {
    position: absolute; left: 0; right: 0; top: 356px; text-align: center;
    font-family: "Cinzel", Georgia, serif; font-weight: 600;
    font-size: 22px; line-height: 28px; letter-spacing: 1px; color: var(--white);
  }
</style>
</head>
<body>
  <section class="card card-front">
    <h1 class="person-name">Maren Holt</h1>
    <p class="person-title">Trial Lawyer</p>

    <ul class="contact-list">
      <li>
        <svg class="contact-icon" viewBox="0 0 24 24" aria-hidden="true"><path d="M6.6 10.8a15.1 15.1 0 0 0 6.6 6.6l2.2-2.2a1 1 0 0 1 1-.25 11.4 11.4 0 0 0 3.6.57 1 1 0 0 1 1 1V20a1 1 0 0 1-1 1A17 17 0 0 1 3 4a1 1 0 0 1 1-1h3.5a1 1 0 0 1 1 1c0 1.25.2 2.45.57 3.57a1 1 0 0 1-.25 1z"/></svg>
        (555) 014-2387
      </li>
      <li>
        <svg class="contact-icon" viewBox="0 0 24 24" aria-hidden="true"><path d="M2 5h20v14H2z"/><path d="M3.5 6.5l8.5 6 8.5-6" fill="none" stroke="#fff" stroke-width="1.6"/></svg>
        maren@vernac-law.example
      </li>
      <li>
        <svg class="contact-icon" viewBox="0 0 24 24" aria-hidden="true"><circle cx="12" cy="12" r="10"/><path d="M2 12h20M12 2c3 3 3 17 0 20M12 2c-3 3-3 17 0 20" fill="none" stroke="#fff" stroke-width="1.4"/></svg>
        www.vernac-law.example
      </li>
    </ul>

    <ul class="practice-list">
      <li>Criminal Law</li>
      <li>Civil Litigation/Personal Injury</li>
      <li>Restraining</li>
    </ul>

    <p class="firm-name">Vernac Law</p>
  </section>

  <section class="card card-back">
    <p class="firm-name-large">Vernac Law</p>
    <p class="tagline">CLARITY. COUNSEL. COMMITMENT.</p>
  </section>
</body>
</html>
```